13 Varno - new website design project

Our company Varno Electrical is developing a new lead generation website focused on Electrical, LED Lighting and Solar Power. We need a high converting website.

Example of our current website is www.varnoelectrical-example.com.au You can take content from this website for this new design. Our colours are red, black and white. For our new website we would like to promote Varno, Spark Every Day. Please listen to the jingle.

The below link is the company jingle that we have developed.
http://www.tunecraftdemo.com.au/vrn-tc-v1/

The key for this brief is to generate leads for Electrical, LED Lighting (for commercial) and Solar Power & Storage.

Target Market(s)

Business owners in Melbourne Victoria

Number of Pages Required

4 page

Colors
ec1f27
ffffff

Requirements
Must have
• This page must be clean, be in line with company branding and a high converting lead website.

```html
<!DOCTYPE html>
<html lang="en">
<head>
<meta charset="utf-8">
<title>Varno Electrical</title>
<link href="https://fonts.googleapis.com/css2?family=Exo+2:ital,wght@0,300;0,400;0,500;0,600;1,300;1,400&family=Arimo:ital,wght@0,400;0,700;1,400&display=swap" rel="stylesheet">
<style>
:root{
  --red:#d9222a;
  --red-dark:#b51b22;
  --black:#1b1b1d;
  --charcoal:#2e3034;
  --slate:#3b3e44;
  --grey:#ececec;
  --mid:#8a8a8a;
  --white:#ffffff;
  --text:#333333;
}
*{box-sizing:border-box;margin:0;padding:0}
html,body{width:1200px;height:4167px;overflow:hidden}
body{font-family:"Arimo",Arial,sans-serif;color:var(--text);background:var(--white);position:relative}
.abs{position:absolute}
.heading{font-family:"Exo 2",sans-serif;font-weight:400;text-transform:uppercase;text-align:center;font-size:46px;line-height:1.2;letter-spacing:1px;color:var(--black)}
.heading em{font-style:normal;color:var(--red);font-weight:500}
.btn{position:absolute;display:flex;align-items:center;font-family:"Exo 2",sans-serif;font-size:19px;color:var(--white);text-transform:uppercase;border-radius:4px;overflow:hidden}
.btn span{background:var(--red);height:100%;display:flex;align-items:center;padding:0 18px;flex:1;justify-content:center}
.btn i{background:var(--charcoal);width:50px;height:100%;display:flex;align-items:center;justify-content:center;font-style:normal}

/* header */
.topline{top:8px;right:78px;font-size:17px;color:var(--text);display:flex;align-items:center;gap:10px}
.logo{left:78px;top:30px;display:flex;align-items:center;gap:14px}
.logo .mark{width:70px;height:70px;border-radius:50%;background:var(--red)}
.logo .name{font-family:"Exo 2",sans-serif;font-weight:600;font-size:54px;color:var(--black);letter-spacing:2px}
.call{left:611px;top:64px;display:flex;gap:14px;align-items:center}
.call small{display:block;font-size:16px;color:var(--text)}
.call b{display:block;font-family:"Exo 2",sans-serif;font-size:28px;color:var(--red)}
.search{left:828px;top:69px;width:294px;height:48px;display:flex}
.search div{flex:1;border:1px solid #cfcfcf;font-size:15px;color:var(--mid);padding:14px 12px}
.search span{width:44px;background:var(--red);display:flex;align-items:center;justify-content:center}
.nav{top:153px;left:0;width:1200px;height:47px;background:var(--charcoal);display:flex;padding-left:83px}
.nav a{font-family:"Exo 2",sans-serif;font-size:17px;color:var(--white);text-decoration:none;padding:0 16px;display:flex;align-items:center;text-transform:uppercase}
.nav a.active{background:var(--red);padding:0 30px}

/* hero */
.hero{top:200px;left:0;width:1200px;height:489px;background:linear-gradient(90deg,#2a2a2c 0%,#4a4744 45%,#9b8e84 70%,#c9c2ba 100%)}
.hero-title{left:78px;top:358px;font-family:"Exo 2",sans-serif;font-style:italic;font-weight:300;font-size:58px;line-height:1;color:var(--red);letter-spacing:1px}
.hero-sub{left:78px;top:434px;width:420px;font-style:italic;font-size:21px;color:var(--white);line-height:1.3}
.hero-arrow{top:430px;color:#ccc;font-size:30px}

/* welcome */
.welcome{top:689px;left:0;width:1200px;height:250px;background:var(--red);color:var(--white);text-align:center}
.welcome .heading{margin-top:42px;color:var(--black)}
.welcome .heading em{color:var(--white)}
.welcome p{width:900px;margin:16px auto 0;font-size:15.5px;line-height:1.75}

/* services */
.card{top:1083px;width:325px}
.card .photo{width:278px;height:278px;border-radius:50%;margin:0 auto;background:radial-gradient(circle at 50% 40%,#c9ced4,#5b5f66)}
.card .box{position:absolute;top:173px;left:0;width:325px;height:170px;background:var(--charcoal);color:var(--white);text-align:center;padding:18px 24px;border-bottom:10px solid #9a9a9a;border-radius:6px 6px 0 0}
.card .box h3{font-family:"Exo 2",sans-serif;font-weight:400;font-size:24px;text-transform:uppercase;margin-bottom:10px}
.card .box p{font-size:14.5px;line-height:1.55}
.card.red .box{background:var(--red)}
.card.red .photo{border:5px solid var(--red)}

/* about */
.about{top:1492px;left:0;width:1200px;height:419px;background:linear-gradient(90deg,#101012,#2a2b2e 60%,#1a1a1c)}
.about-text{left:78px;top:1546px;width:580px;color:#d8d8d8}
.about-text .heading{text-align:left;color:var(--white)}
.about-text h4{font-style:italic;font-weight:400;font-size:16px;margin:2px 0 10px}
.about-text p{font-size:14.5px;line-height:1.6;margin-bottom:8px}
.video{left:683px;top:1558px;width:439px;height:292px;background:linear-gradient(135deg,#9ea7ae,#5c6770);border:4px solid var(--white)}

/* music */
.music{top:1911px;left:0;width:1200px;height:167px;background:var(--red)}
.music .heading{position:absolute;left:78px;top:40px;color:var(--black)}
.music .heading em{color:var(--white);font-weight:400}
.music p{position:absolute;left:78px;top:102px;color:var(--white);font-size:17px}
.outline-btn{left:908px;top:1969px;height:56px;width:214px;display:flex;border-radius:4px;overflow:hidden}
.outline-btn span{flex:1;border:2px solid var(--white);border-right:none;color:var(--white);font-family:"Exo 2",sans-serif;font-size:19px;display:flex;align-items:center;justify-content:center;border-radius:4px 0 0 4px}
.outline-btn i{width:50px;background:var(--charcoal);color:var(--white);font-style:normal;display:flex;align-items:center;justify-content:center}

/* work */
.work-img{top:2217px;height:161px;background:linear-gradient(180deg,#f4f4f4 0%,#f4f4f4 28%,#7d8790 30%,#44494f 100%);position:absolute}
.work-img .brand{position:absolute;top:8px;left:10px;font-family:"Exo 2",sans-serif;font-weight:600;font-size:20px;color:var(--charcoal)}
.quote{top:2217px;font-size:14.5px;line-height:1.6;color:#666}
.quote b{display:block;color:var(--red);font-weight:400;margin-top:18px}
.quote span{color:var(--black)}
.pager{top:2416px;width:44px;height:44px;border:1px solid #ccc;display:flex;align-items:center;justify-content:center;color:#999}

/* why */
.why{top:2522px;left:0;width:1200px;height:639px;background:linear-gradient(90deg,#c8202a,#a8161f)}
.bulb{left:83px;top:2555px;width:445px;height:598px;background:radial-gradient(circle at 55% 38%,#f3e9e0 0%,#e6c9bd 28%,rgba(200,32,42,0) 60%)}
.why .heading{position:absolute;left:536px;top:60px;text-align:left;color:var(--white);font-weight:300}
.why .heading em{color:var(--black);font-weight:500}
.why-list{left:536px;top:2654px;width:586px;color:var(--white)}
.why-list li{list-style:none;display:flex;gap:14px;margin-bottom:22px}
.why-list h5{font-family:"Exo 2",sans-serif;font-weight:500;font-size:21px;margin-bottom:6px}
.why-list p{font-size:14px;line-height:1.6;color:#f3d3d4}

/* clients */
.clients{top:3161px;left:0;width:1200px;height:172px;background:var(--grey)}
.client{top:3208px;width:166px;height:92px;background:var(--white);display:flex;align-items:center;justify-content:center;gap:10px;font-family:"Exo 2",sans-serif;font-weight:600;font-size:21px;color:var(--charcoal)}
.client i{width:14px;height:14px;background:var(--red);display:block}

/* contact */
.contact-title{top:3396px;left:0;width:1200px}
.contact-lead{top:3458px;left:186px;width:828px;text-align:center;font-size:15px;line-height:1.6}
.field{border:1px solid #cfcfcf;font-size:14.5px;color:var(--mid);padding:14px 12px}

/* footer */
.footer{top:3820px;left:0;width:1200px;height:291px;background:linear-gradient(180deg,#1c1c1e,#121213)}
.social{top:4016px;width:46px;height:46px;border-radius:50%;border:2px solid #666}
.social.red{background:var(--red);border-color:var(--red)}
.fcol{top:3858px;color:#c9c9c9;font-size:14.5px;line-height:1.7;width:240px}
.fcol h6{font-family:"Exo 2",sans-serif;font-weight:500;font-size:19px;color:var(--red);text-transform:uppercase;margin-bottom:6px}
.fcol .r{color:var(--red)}
.fcol .mail{font-size:12.5px}
.fcol.news{line-height:1.55}
.legal{top:4111px;left:0;width:1200px;height:56px;background:var(--red);color:var(--white);font-size:15px;display:flex;align-items:center;justify-content:center;gap:6px}
</style>
</head>
<body>

<header>
  <div class="abs topline">
    <svg width="18" height="14" viewBox="0 0 18 14"><rect x="1" y="1" width="16" height="12" fill="none" stroke="#333" stroke-width="1.6"/><path d="M1 1l8 7 8-7" fill="none" stroke="#333" stroke-width="1.6"/></svg>
    service@varnoelectrical-example.com.au
  </div>
  <div class="abs logo"><span class="mark"></span><span class="name">VARNO</span></div>
  <div class="abs call">
    <svg width="44" height="44" viewBox="0 0 24 24"><path d="M6.6 10.8c1.4 2.8 3.8 5.1 6.6 6.6l2.2-2.2c.3-.3.7-.4 1-.2 1.1.4 2.3.6 3.6.6.6 0 1 .4 1 1V20c0 .6-.4 1-1 1C10.6 21 3 13.4 3 4c0-.6.4-1 1-1h3.5c.6 0 1 .4 1 1 0 1.3.2 2.5.6 3.6.1.3 0 .7-.2 1z" fill="#d9222a"/></svg>
    <div><small>Call Us On Varno</small><b>139406</b></div>
  </div>
  <div class="abs search"><div>Search...</div><span><svg width="18" height="18" viewBox="0 0 18 18"><circle cx="7.5" cy="7.5" r="5.5" fill="none" stroke="#fff" stroke-width="2.2"/><path d="M11.5 11.5L16 16" stroke="#fff" stroke-width="2.4"/></svg></span></div>
  <nav class="abs nav">
    <a class="active">Home</a><a>Varno Story</a><a>Our Work</a><a>Electrical</a><a>LED Lighting</a><a>Solar Power</a><a>Contact Us</a>
  </nav>
</header>

<section>
  <div class="abs hero" role="img" aria-label="Electrician in red work shirt wiring a switchboard"></div>
  <div class="abs hero-arrow" style="left:24px">&#8249;</div>
  <div class="abs hero-arrow" style="right:24px">&#8250;</div>
  <h1 class="abs hero-title">MORE POWER TO YOU</h1>
  <p class="abs hero-sub">Australia's largest fully integrated electrical &amp; Energy Solutions provider.</p>
  <div class="btn" style="left:78px;top:505px;width:214px;height:58px"><span>Contact Us</span><i>&#187;</i></div>
</section>

<section class="abs welcome">
  <h2 class="heading">Welcome to <em>Varno</em></h2>
  <p>Varno Electrical was formed to be an expert Electricity Contracting Company providing services to all Residential and Commercial Customers. With over 10 years of experience, Varno Electrical has developed a highly-experienced team of professionals that ensure all our customer expectations are met.</p>
  <svg style="margin-top:10px" width="22" height="22" viewBox="0 0 22 22"><path d="M4 4l7 6 7-6M4 11l7 6 7-6" fill="none" stroke="#fff" stroke-width="2"/></svg>
</section>

<section>
  <h2 class="heading abs" style="top:990px;left:0;width:1200px">Our <em>Services</em></h2>
  <div class="abs card red" style="left:83px">
    <div class="photo" role="img" aria-label="Hands wiring a power point"></div>
    <div class="box"><h3>Electrical</h3><p>Melbourne wide , Quick Response time , Electrical Services provide by experienced electricians</p></div>
  </div>
  <div class="abs card" style="left:436px">
    <div class="photo" role="img" aria-label="Warehouse ceiling with LED high bay lights"></div>
    <div class="box"><h3>LED Lighting</h3><p>Upgrading your business to LED Lighting is one of the quickest ways to slash the operating costs of your business.</p></div>
  </div>
  <div class="abs card" style="left:794px">
    <div class="photo" role="img" aria-label="Rooftop solar panels under a clear sky"></div>
    <div class="box"><h3>Solar Power</h3><p>Confirm Rebate Eligibility , Get A Return on Investment Report , See Samples And Get best pricing.</p></div>
  </div>
</section>

<section>
  <div class="abs about"></div>
  <div class="abs about-text">
    <h2 class="heading">About <em>Varno</em></h2>
    <h4>Spark Every Day</h4>
    <p>Varno Electrical was formed to be an expert Electricity Contracting Company providing services to all Residential and Commercial Customers. With over 10 years of experience, Varno Electrical has developed a highly-experienced team of professionals that ensure all our customer expectations are met.</p>
    <p>Varno Electrical was formed to be an expert Electricity Contracting Company providing services to all Residential and Commercial Customers.</p>
  </div>
  <div class="btn" style="left:78px;top:1810px;width:214px;height:56px"><span>Know More</span><i>&#187;</i></div>
  <div class="abs video" role="img" aria-label="Video still of an electrician in a hard hat checking a switchboard">
    <svg style="position:absolute;left:175px;top:116px" width="80" height="56" viewBox="0 0 80 56"><rect width="80" height="56" rx="12" fill="#d9222a"/><path d="M32 16l20 12-20 12z" fill="#fff"/></svg>
  </div>
</section>

<section class="abs music">
  <h2 class="heading">Varno <em>Brand Music</em></h2>
  <p>What Does your brand sound like ?</p>
</section>
<div class="abs outline-btn"><span>SUBSCRIBE</span><i>&#187;</i></div>

<section>
  <h2 class="heading abs" style="top:2126px;left:0;width:1200px">Our <em>Work</em></h2>
  <div class="work-img" style="left:78px;width:227px" role="img" aria-label="Signage workshop building"><span class="brand">HARLOW SIGNS</span></div>
  <div class="abs quote" style="left:322px;width:267px">I found Daniel to be well organised, punctual, professional and a good communicator. He did the job at a very reasonable price. A pleasure.<b>- Marco T.</b><span>Mount Waverley VIC</span></div>
  <div class="work-img" style="left:608px;width:222px" role="img" aria-label="Industrial steel warehouse"><span class="brand">nordsteel</span></div>
  <div class="abs quote" style="left:850px;width:272px">"Excellent work and very professional. Daniel takes time to explain everything and demonstrate workings. Very clear precise and accurate."<b>- Pelham</b><span>Cranbourne North VIC</span></div>
  <div class="abs pager" style="left:550px">&#8249;</div>
  <div class="abs pager" style="left:604px">&#8250;</div>
</section>

<section class="abs why">
  <h2 class="heading">Why Choose <em>Us ?</em></h2>
</section>
<div class="abs bulb" role="img" aria-label="Hand touching a glowing light bulb with a satisfaction guaranteed badge"></div>
<ul class="abs why-list">
  <li><svg width="22" height="22" viewBox="0 0 22 22"><path d="M3 19L11 3l8 16" fill="none" stroke="#fff" stroke-width="2.4"/></svg><div><h5>Professional service</h5><p>When you hire a Varno Electrical Electrician you will get a professional and well-presented Electrician that comes skilled and ready to do the job.</p></div></li>
  <li><svg width="22" height="22" viewBox="0 0 22 22"><path d="M3 19L11 3l8 16" fill="none" stroke="#fff" stroke-width="2.4"/></svg><div><h5>5 year workmanship guarantee</h5><p>You can buy with confidence as all of our work has a 5 year workmanship guarantee. For your peace of mind, we unconditionally back our electrical work.</p></div></li>
  <li><svg width="22" height="22" viewBox="0 0 22 22"><path d="M3 19L11 3l8 16" fill="none" stroke="#fff" stroke-width="2.4"/></svg><div><h5>Value for Money</h5><p>We provide extremely competitive pricing, which means you get value for money on quality that is comparable to the best in the industry.</p></div></li>
  <li><svg width="22" height="22" viewBox="0 0 22 22"><path d="M3 19L11 3l8 16" fill="none" stroke="#fff" stroke-width="2.4"/></svg><div><h5>Environmentally friendly</h5><p>We a committed to reducing carbon emissions by installing Solar Power and upgrading sites to LED Lighting.</p></div></li>
  <li><svg width="22" height="22" viewBox="0 0 22 22"><path d="M3 19L11 3l8 16" fill="none" stroke="#fff" stroke-width="2.4"/></svg><div><h5>Fully insured</h5><p>Fully insured &amp; equipped to handle break downs &amp; service call outs.</p></div></li>
</ul>

<section>
  <div class="abs clients"></div>
  <div class="abs client" style="left:208px"><i></i>Brightmart</div>
  <div class="abs client" style="left:417px"><i></i>Keel Plumbing</div>
  <div class="abs client" style="left:620px"><i></i>Burgerly</div>
  <div class="abs client" style="left:828px"><i></i>Outpost Gear</div>
</section>

<section>
  <h2 class="heading abs contact-title">Contact <em>Us</em></h2>
  <p class="abs contact-lead">Lorem Ipsum is simply dummy text of the printing and typesetting industry. Lorem Ipsum has been the industry's standard dummy text ever since the 1500s, when an unknown printer took.</p>
  <div class="abs field" style="left:186px;top:3528px;width:269px;height:48px">Name*</div>
  <div class="abs field" style="left:472px;top:3528px;width:261px;height:48px">Email*</div>
  <div class="abs field" style="left:744px;top:3528px;width:270px;height:48px">Phone*</div>
  <div class="abs field" style="left:186px;top:3586px;width:828px;height:108px">Message*</div>
  <div class="btn" style="left:514px;top:3703px;width:166px;height:55px"><span>Submit</span><i>&#187;</i></div>
</section>

<footer>
  <div class="abs footer"></div>
  <div class="abs social red" style="left:117px"></div>
  <div class="abs social" style="left:171px"></div>
  <div class="abs social" style="left:235px"></div>
  <div class="abs fcol" style="left:344px">
    <h6>Sitemap</h6>
    &raquo; Home<br>&raquo; Varno Story<br>&raquo; Our work<br>&raquo; Electrical<br>&raquo; Led Lighting<br>&raquo; Solar Power<br>&raquo; Contact Us
  </div>
  <div class="abs fcol" style="left:608px">
    <h6>Get in touch</h6>
    <span class="r">Varno Spark Every Day</span><br>12/48 Linton Rd<br>Glenvale<br>VIC 3199<br>139406<br><span class="mail">service@varnoelectrical-example.com.au</span>
  </div>
  <div class="abs fcol news" style="left:872px;width:250px">
    <h6>Newsletter</h6>
    Would you like to receive exclusive access to articles, white papers and our regular monthly newsletter?
  </div>
  <div class="abs field" style="left:872px;top:3994px;width:250px;height:44px;background:#fff;color:#555">Enter Email Id</div>
  <div class="btn" style="left:872px;top:4046px;width:170px;height:44px"><span>Subscribe</span><i>&#187;</i></div>
  <div class="abs legal"><b>VARNO SPARK EVERY DAY</b> &copy; 2017. All Rights Reserved. | Terms and Conditions Privacy</div>
</footer>

</body>
</html>
```